Construction Company Cellar Crafters needs Business Card

I would like modern looking business card design. I am attaching logo of our company. Please include cell nr 302.418.7650 , email address cellarcrafters4u@examplemail.com, web : cellarcrafters4u.com, please also include wording: Specializing in finishing and remodeling basements. You can play with dark grey and orange colors or any ideas are welcome. Also include social media icons Friendloop and HouseGuidr.

```html
<!DOCTYPE html>
<html lang="en">
<head>
<meta charset="utf-8">
<title>Cellar Crafters – Business Card</title>
<link href="https://fonts.googleapis.com/css2?family=PT+Sans:wght@400;700&family=Exo+2:wght@500&display=swap" rel="stylesheet">
<style>
  :root {
    --card-dark: #1d1d1d;
    --accent-orange: #f05a28;
    --text-white: #ffffff;
    --backdrop: #e9e7e4;
  }
  * { margin: 0; padding: 0; box-sizing: border-box; }
  html, body { width: 1200px; height: 900px; overflow: hidden; }
  body {
    background: var(--backdrop);
    font-family: "PT Sans", sans-serif;
    position: relative;
  }
  .card {
    position: absolute;
    background: var(--card-dark);
    color: var(--text-white);
    overflow: hidden;
  }
  .card-front { left: 238px; top: 60px; width: 555px; height: 345px; }
  .card-back { left: 457px; top: 518px; width: 560px; height: 344px; }

  .stripes { position: absolute; inset: 0; }

  .holder { position: absolute; left: 34px; top: 30px; }
  .holder-name { font-size: 19px; font-weight: 700; line-height: 1.2; }
  .holder-title { font-size: 15px; line-height: 1.3; }

  .contact-list {
    position: absolute; left: 32px; top: 141px;
    list-style: none; font-size: 15px; line-height: 20px;
  }
  .contact-list li { display: flex; align-items: center; gap: 8px; }
  .contact-list svg { width: 12px; height: 12px; fill: var(--text-white); flex: none; }

  .social-links {
    position: absolute; left: 33px; top: 280px;
    display: flex; gap: 16px; font-size: 14px; font-weight: 700;
  }

  .brand {
    position: absolute; left: 0; right: 0; top: 140px;
    text-align: center;
    font-family: "Exo 2", sans-serif; font-weight: 500;
    font-size: 50px; letter-spacing: 1px;
    color: var(--accent-orange); text-transform: uppercase;
  }
  .tagline {
    position: absolute; left: 0; right: 0; top: 274px;
    text-align: center; font-size: 15px;
    color: var(--accent-orange); text-transform: uppercase; letter-spacing: 0.2px;
  }
</style>
</head>
<body>
  <section class="card card-front">
    <svg class="stripes" viewBox="0 0 555 345" aria-hidden="true">
      <g fill="var(--accent-orange)">
        <polygon points="207,345 245,345 545,0 507,0"/>
        <polygon points="284,345 330,345 630,0 584,0"/>
        <polygon points="372,345 418,345 718,0 672,0"/>
        <polygon points="462,345 508,345 808,0 762,0"/>
      </g>
    </svg>
    <div class="holder">
      <div class="holder-name">Daniel Hartley</div>
      <div class="holder-title">Managing Director</div>
    </div>
    <ul class="contact-list">
      <li><svg viewBox="0 0 24 24"><path d="M6.6 10.8a15.1 15.1 0 0 0 6.6 6.6l2.2-2.2a1 1 0 0 1 1-.25 11.4 11.4 0 0 0 3.6.57 1 1 0 0 1 1 1V20a1 1 0 0 1-1 1A17 17 0 0 1 3 4a1 1 0 0 1 1-1h3.5a1 1 0 0 1 1 1c0 1.25.2 2.45.57 3.57a1 1 0 0 1-.25 1z"/></svg>302.418.7650</li>
      <li><svg viewBox="0 0 24 24"><path d="M2 5h20v14H2z M2 5l10 8 10-8" fill="var(--text-white)"/><path d="M3 6l9 7 9-7" stroke="var(--card-dark)" stroke-width="2" fill="none"/></svg>cellarcrafters4u@examplemail.com</li>
      <li><svg viewBox="0 0 24 24"><circle cx="12" cy="12" r="10"/><path d="M2 12h20M12 2c3 3 3 17 0 20M12 2c-3 3-3 17 0 20" stroke="var(--card-dark)" stroke-width="1.5" fill="none"/></svg>cellarcrafters4u.com</li>
    </ul>
    <div class="social-links">
      <span class="social-name">Friendloop</span>
      <span class="social-name">HouseGuidr</span>
    </div>
  </section>

  <section class="card card-back">
    <div class="brand">Cellar Crafters</div>
    <p class="tagline">Specializing in finishing and remodeling basements.</p>
  </section>
</body>
</html>
```